Moldran Foods needs a new label for canned pineapple

We want a very tasty (in terms of making your mouth water) and clean design (less is more) for our canned pineapple under the new logo of Moldran Leafline division

Target Market(s)

The company’s mission is to bring quality food to target audiences of any social status (you receive a bit more than what you spend). Our core values are: reliability, loyalty and commitment to development.
The product is sold to mainstream and lower Mainstream customers.

Requirements
Must have
• The design should take into consideration the visibility on the shelf among competitor products (brief file) and that the product is a MAINSTREAM product.
We want a very tasty (in terms of making your mouth water) and clean design (less is more). The design should be easily modifiable for other canned fruits or vegetables.
The package must display on the front the following elements listed in the order of their should have noticeability:
• Moldran Leaf logo
• Pineapple picture
• Product name
Designers should take into account that the shelfs for displaying the products in the shops may have an elevation of up to 3 cm that can overlap the product label.

Guidelines
• We would like the packaging to be as simple as possible (or at least not to sabotage the Moldran name ), as our strategy depends on the agressive communication of the Moldran logo.
• We would also like to communicate through suggestive and optimal colours as to be easily spotted on the shelf.
• As we have quite a minimal communication budget we need basically for the packaging to do a lot of the communication job itself
• FMCG is a highly visual industry so we have to include pictures of the products on the packages (even more than others do, as we are focused on health and quality - we want people to have that feeling of fresh products even though we are selling canned ones)
Should not have
• but the minimum amount of text on the front.

```html
<!DOCTYPE html>
<html lang="ro">
<head>
<meta charset="utf-8">
<title>Moldran Leafline – Ananas felii</title>
<link rel="stylesheet" href="https://fonts.googleapis.com/css2?family=Open+Sans:wght@600;700;800&display=swap">
<style>
  :root {
    --backdrop: #e4e4e4;
    --label-white: #ffffff;
    --brand-green: #1f7a32;
    --fruit-red: #ee1111;
    --red-light: #ff8a8a;
    --red-bright: #ff0000;
    --red-deep: #a30000;
    --pineapple-white: #f4f4f4;
  }
  * { margin: 0; padding: 0; box-sizing: border-box; }
  html, body {
    width: 1200px;
    height: 900px;
    overflow: hidden;
    background: var(--backdrop);
    font-family: "Open Sans", Arial, sans-serif;
  }
  .label {
    position: absolute;
    left: 275px;
    top: 67px;
    width: 650px;
    height: 766px;
    display: flex;
  }
  .info-panel {
    position: relative;
    width: 278px;
    height: 100%;
    background: var(--label-white);
  }
  .brand-mark {
    position: absolute;
    left: 40px;
    top: 116px;
    width: 210px;
    display: flex;
    align-items: center;
    gap: 10px;
  }
  .brand-dot {
    width: 22px;
    height: 22px;
    border-radius: 50%;
    background: var(--brand-green);
    flex: none;
  }
  .brand-name {
    color: var(--brand-green);
    font-weight: 700;
    font-size: 30px;
    line-height: 1.05;
  }
  .product-title {
    position: absolute;
    left: 38px;
    top: 330px;
    color: var(--fruit-red);
    font-weight: 800;
    font-size: 44px;
    line-height: 0.95;
    letter-spacing: -2px;
  }
  .product-subtitle {
    position: absolute;
    left: 38px;
    top: 414px;
    color: var(--fruit-red);
    font-weight: 600;
    font-size: 19px;
    letter-spacing: -0.5px;
  }
  .title-rule {
    position: absolute;
    left: 38px;
    top: 442px;
    width: 240px;
    height: 2px;
    background: var(--fruit-red);
  }
  .net-weight {
    position: absolute;
    left: 48px;
    top: 690px;
    color: var(--fruit-red);
    font-weight: 700;
    font-size: 32px;
  }
  .fruit-panel {
    position: relative;
    width: 372px;
    height: 100%;
    background: linear-gradient(90deg, var(--red-light) 0%, var(--red-bright) 28%, var(--red-bright) 55%, var(--red-deep) 100%);
  }
  .pineapple-art {
    position: absolute;
    left: 72px;
    top: 130px;
    width: 228px;
    height: 460px;
  }
</style>
</head>
<body>
  <main class="label">
    <section class="info-panel">
      <div class="brand-mark">
        <span class="brand-dot"></span>
        <span class="brand-name">Moldran Leafline</span>
      </div>
      <h1 class="product-title">ANANAS<br>FELII</h1>
      <p class="product-subtitle">in suc indulcit</p>
      <div class="title-rule"></div>
      <p class="net-weight">258 g</p>
    </section>
    <section class="fruit-panel">
      <svg class="pineapple-art" viewBox="0 0 228 460" role="img" aria-label="White stylised pineapple illustration with crown leaves">
        <rect x="0" y="0" width="228" height="460" rx="40" fill="var(--pineapple-white)"/>
      </svg>
    </section>
  </main>
</body>
</html>
```